Modern looking signage for dental office.

Exterior signage for passing cars
Updates
Need extra days to review
Target Market(s)
Cars passing by
Font styles to use
Sans Serif
Colors
3276b5
Requirements
Must have
- Logo
- OPEN ON SUTURDAY AND SUNDAY
- NIGHT CLINIC AVAILABLE
- PLEASE USE THE FONT TYPE IN FILE 4 UPLOADED BELOW.
- (847) 302-7469
- Modern looking

```html
<!DOCTYPE html>
<html lang="en">
<head>
<meta charset="utf-8">
<title>Brio Dental – Exterior Sign</title>
<link rel="stylesheet" href="https://fonts.googleapis.com/css2?family=Open+Sans:ital,wght@0,300;0,700;1,700&family=Encode+Sans+Semi+Condensed:wght@400&display=swap">
<style>
  :root {
    --teal: #0a85a0;
    --teal-dark: #06606f;
    --white: #ffffff;
    --ink: #231f20;
    --grey: #545151;
    --grey-light: #5f5d5d;
  }
  html, body {
    margin: 0;
    padding: 0;
    width: 1200px;
    height: 800px;
    overflow: hidden;
    background: var(--white);
  }
  .sign {
    display: block;
    width: 1200px;
    height: 800px;
  }
  .sign__ground { fill: var(--teal); }
  .sign__panel { fill: var(--white); }
  .sign__panel-shadow { fill: var(--teal-dark); }
  .brand__ring { fill: none; stroke: var(--grey); stroke-width: 3; }
  .brand__name {
    font-family: "Open Sans", sans-serif;
    font-weight: 300;
    fill: var(--grey);
  }
  .brand__tagline {
    font-family: "Encode Sans Semi Condensed", sans-serif;
    font-weight: 400;
    fill: var(--grey-light);
  }
  .hours__open {
    font-family: "Open Sans", sans-serif;
    font-style: italic;
    font-weight: 700;
    fill: var(--teal);
  }
  .hours__text {
    font-family: "Open Sans", sans-serif;
    font-weight: 700;
    fill: var(--white);
  }
  .contact__phone {
    font-family: "Open Sans", sans-serif;
    font-weight: 700;
    fill: var(--ink);
  }
</style>
</head>
<body>
<svg class="sign" viewBox="0 0 1200 800" xmlns="http://www.w3.org/2000/svg" role="img" aria-label="Brio Dental sign: open on Saturday and Sunday, night clinic available, call (847) 302-7469">
  <rect class="sign__ground" x="0" y="0" width="1200" height="800"/>

  <!-- upper white panel with slash divider -->
  <rect class="sign__panel" x="22" y="20" width="1138" height="450"/>
  <polygon class="sign__panel" points="612,469 634,469 598,611 579,611"/>

  <!-- lower phone panel with curved edge -->
  <path class="sign__panel-shadow" d="M22 610 H1146 C1100 700 1020 756 940 764 H22 Z"/>
  <path class="sign__panel" d="M22 610 H1136 C1090 700 1010 756 928 764 H22 Z"/>

  <!-- brand -->
  <g class="brand">
    <circle class="brand__ring" cx="170" cy="188" r="120"/>
    <text class="brand__name" x="312" y="238" font-size="140" textLength="832" lengthAdjust="spacingAndGlyphs">BRIO DENTAL</text>
    <text class="brand__tagline" x="394" y="312" font-size="54" textLength="640" lengthAdjust="spacingAndGlyphs">MODERN GENERAL DENTISTRY</text>
  </g>

  <!-- opening hours -->
  <g class="hours">
    <text class="hours__open" x="610" y="442" font-size="68" text-anchor="middle">Open</text>
    <text class="hours__text" x="306" y="524" font-size="40" text-anchor="middle">on</text>
    <text class="hours__text" x="46" y="580" font-size="52" textLength="518" lengthAdjust="spacingAndGlyphs">Saturday &amp; Sunday</text>
    <text class="hours__text" x="652" y="554" font-size="48" textLength="484" lengthAdjust="spacingAndGlyphs">Night clinic available</text>
  </g>

  <!-- contact -->
  <text class="contact__phone" x="74" y="724" font-size="136" textLength="858" lengthAdjust="spacingAndGlyphs">(847) 302-7469</text>
</svg>
</body>
</html>
```